Varnex Consulting Business card design.

See our website www.varnexconsulting.example which will give you a good idea of what we are about. The font is called 'Play'.

I'd like a standout business card in keeping with the themes and branding on the website

Target Market(s)

professionals. HR directors

Industry/Entity Type

Business

Contact Information for Business Card

Varnex Consulting PO Box 3172 Merrowdale NSW 2291 1300 485 193 Gavin Threlkeld Principal email: career@varnexconsulting.example ABN: 71203948865

Font styles to use
Other font styles liked:
• Play

Requirements
Must have
• Must have same design colours and branding as website.
• On back I'd prefer a list of the things we do which appears below the name at the header on the website

```html
<!DOCTYPE html>
<html lang="en">
<head>
<meta charset="utf-8">
<title>Varnex Consulting – Business Card</title>
<link rel="stylesheet" href="https://fonts.googleapis.com/css2?family=Play:wght@400;700&display=swap">
<style>
  :root {
    --navy: #15283b;
    --blue: #2b93da;
    --paper: #fbfbfb;
    --backdrop: #aeacad;
    --ink: #1f2b36;
  }
  * { box-sizing: border-box; margin: 0; padding: 0; }
  html, body { width: 1200px; height: 1200px; overflow: hidden; }
  body {
    background: var(--backdrop);
    font-family: "Play", sans-serif;
    color: var(--ink);
    position: relative;
  }
  .card {
    position: absolute;
    left: 244px;
    width: 712px;
    height: 419px;
    background: var(--paper);
    overflow: hidden;
  }
  .card--front { top: 118px; }
  .card--back { top: 644px; }

  /* Front */
  .front-wordmark {
    position: absolute;
    top: 128px;
    left: 0; right: 0;
    text-align: center;
    font-size: 60px;
    line-height: 1;
    color: var(--navy);
    letter-spacing: 0.5px;
  }
  .front-services {
    position: absolute;
    top: 200px;
    left: 0; right: 0;
    text-align: center;
    font-size: 15px;
    letter-spacing: 2.2px;
    color: var(--blue);
  }
  .front-web {
    position: absolute;
    top: 344px;
    left: 0; right: 0;
    display: flex;
    justify-content: center;
    align-items: center;
    gap: 12px;
    font-size: 18px;
    color: var(--navy);
  }
  .front-web .rule { width: 34px; height: 2px; background: var(--blue); border-radius: 2px; }

  /* Back */
  .back-wordmark {
    position: absolute;
    left: 46px;
    top: 136px;
    color: var(--navy);
    line-height: 1;
  }
  .back-wordmark .line-1 { display: block; font-size: 60px; letter-spacing: 1px; }
  .back-wordmark .line-2 { display: block; font-size: 42px; margin-top: 6px; letter-spacing: 1.2px; }
  .contact {
    position: absolute;
    left: 352px;
    top: 84px;
  }
  .contact-name { font-size: 23px; font-weight: 700; color: var(--blue); }
  .contact-role { font-size: 15px; margin-top: 6px; }
  .contact-list { list-style: none; margin-top: 14px; }
  .contact-list li {
    display: flex; align-items: center; gap: 17px;
    font-size: 17px; height: 26px;
  }
  .contact-list svg { width: 17px; height: 14px; fill: var(--blue); }
  .contact-abn { font-size: 17px; margin-top: 5px; }
  .contact-abn .label { color: var(--blue); }
  .contact-address { font-size: 17px; margin-top: 6px; }
  .service-band {
    position: absolute;
    left: 0; right: 0; bottom: 0;
    height: 49px;
    background: var(--navy);
    color: #fff;
    display: flex; align-items: center; justify-content: center;
    font-size: 17px;
    letter-spacing: 1.4px;
  }
</style>
</head>
<body>
  <section class="card card--front">
    <h1 class="front-wordmark">VARNEX CONSULTING</h1>
    <p class="front-services">Search &amp; Select | Career | Coaching | Leadership | Outplacement</p>
    <p class="front-web"><span class="rule"></span>www.varnexconsulting.example<span class="rule"></span></p>
  </section>

  <section class="card card--back">
    <div class="back-wordmark">
      <span class="line-1">VARNEX</span>
      <span class="line-2">CONSULTING</span>
    </div>
    <div class="contact">
      <p class="contact-name">Gavin Threlkeld</p>
      <p class="contact-role">Principal</p>
      <ul class="contact-list">
        <li><svg viewBox="0 0 17 14"><path d="M1 5c0-3 15-3 15 0v2h-4V5H5v2H1z"/><rect x="3" y="8" width="11" height="5" rx="1"/></svg>1300 485 193</li>
        <li><svg viewBox="0 0 17 14"><circle cx="8.5" cy="7" r="6" fill="none" stroke="#2b93da" stroke-width="1.4"/><path d="M2.5 7h12M8.5 1v12" stroke="#2b93da" stroke-width="1.2"/><ellipse cx="8.5" cy="7" rx="2.6" ry="6" fill="none" stroke="#2b93da" stroke-width="1.2"/></svg>www.varnexconsulting.example</li>
        <li><svg viewBox="0 0 17 14"><rect x="1" y="2" width="15" height="10"/><path d="M1 2l7.5 6L16 2" fill="none" stroke="#fbfbfb" stroke-width="1.3"/></svg>career@varnexconsulting.example</li>
      </ul>
      <p class="contact-abn"><span class="label">ABN:</span> 71203948865</p>
      <p class="contact-address">PO Box 3172 Merrowdale NSW 2291</p>
    </div>
    <div class="service-band">Search &amp; Select | Career | Coaching | Leadership | Outplacement</div>
  </section>
</body>
</html>
```